Dog walking/Pet Sitting company needs a brochure to hook high end apartment tenants

We are looking for a brochure design that we can bring to meetings with high-end apartment and hotel management that will explain who we are, what we do, and how we can help their tenants/guests. I would like it to reflect the same look and feel of our website, carried over to printed brochure. Wesbite is www.hollowbrookpawcare.com. I can provide the stock images from the website if needed. A bi-fold brochure is ideal, unless you feel the information would fit better on a tri-fold. My company colors are #5D4664 and #5BA046. I would like a more professional tone to it, rather than fun.

Target Market(s)

Demo Professional Females and Males ages 30-50 with pets

Industry/Entity Type

Pet sitting

Font styles to use
Sans Serif

Colors
6b449b
9bcb3c

Requirements
Must have
• the same look and feel as my website; explain who we are, what we do, how we can help; include services offered; Mention that we service Wrenfield and surrounding towns. Mention 15 years in business.
Should not have
• do not list pricing on brochure (you can mention pricing is available on the website). No cartoonish feel.

```html
<!DOCTYPE html>
<html lang="en">
<head>
<meta charset="utf-8">
<title>Hollowbrook Paw Care – Bi-fold Brochure</title>
<link href="https://fonts.googleapis.com/css2?family=Montserrat:wght@400;500;600;700&display=swap" rel="stylesheet">
<style>
:root{
  --green:#5a9e45;
  --purple:#5a4566;
  --ink:#333333;
  --paper:#ffffff;
  --page-tint:#f7f7f7;
  --backdrop:#e6e6e6;
}
*{box-sizing:border-box;margin:0;padding:0}
html,body{width:800px;height:1200px;overflow:hidden;background:var(--backdrop);font-family:'Montserrat',sans-serif;color:var(--ink)}
.spread{position:absolute;left:53px;width:696px;height:492px;background:var(--paper);overflow:hidden;box-shadow:0 6px 18px rgba(0,0,0,.25)}
.spread--outer{top:55px}
.spread--inner{top:635px;background:var(--page-tint)}
.photo{position:absolute}

/* outer spread */
.band{position:absolute;top:331px;height:161px;background:var(--green);border-top:3px solid var(--purple);color:#fff;text-align:center}
.band--back{left:0;width:348px}
.band--front{left:348px;width:348px}
.band h3{font-size:9.5px;font-weight:600;letter-spacing:.3px;margin-top:24px}
.contact{list-style:none;font-size:6.5px;line-height:12.5px;margin-top:10px}
.contact svg{vertical-align:-1px;margin-right:3px}
.reviews{font-size:6.5px;margin-top:9px}
.review-dots{display:flex;justify-content:center;gap:5px;margin-top:5px}
.review-dots span{width:7px;height:7px;border-radius:50%;background:#fff}
.url{position:absolute;left:0;right:0;bottom:26px;font-size:7.5px;letter-spacing:2.6px}
.tagline-small{font-size:14px;font-weight:500;margin-top:60px}
.tagline-big{font-size:20.5px;font-weight:700;margin-top:7px}
.badge{position:absolute;left:467px;top:271px;width:108px;height:108px;border-radius:50%;background:#fff;border:4px solid var(--green);display:flex;align-items:center;justify-content:center;text-align:center}
.badge span{font-size:10px;font-weight:700;color:var(--purple);line-height:13px;letter-spacing:.5px}
.fold-corner{position:absolute;right:0;bottom:0;width:0;height:0;border-left:14px solid transparent;border-bottom:14px solid var(--purple)}

/* inner spread */
.heading{position:absolute;font-size:13px;font-weight:700;color:var(--purple);letter-spacing:.2px}
.heading em{font-style:normal;color:var(--green)}
.rule{position:absolute;width:12px;height:3px;background:var(--green);border-radius:2px}
.lead{position:absolute;font-size:5.6px;line-height:8px;color:#444}
.mission{position:absolute;left:0;top:115px;width:190px;height:214px;background:var(--green);color:#fff;padding:26px 26px 0 31px}
.mission h4{font-size:13.5px;font-weight:500}
.mission p{font-size:5.5px;line-height:8px;margin:6px 0 14px}
.services{position:absolute;top:353px;left:31px;display:flex;gap:8px}
.service{width:90px;height:116px;background:var(--purple);color:#fff;text-align:center;position:relative}
.service .photo{position:relative;height:54px}
.service h5{background:var(--green);font-size:7px;font-weight:500;height:16px;line-height:16px}
.service p{font-size:4.4px;line-height:6.2px;padding:5px 6px 0}
.pill{position:absolute;left:18px;right:18px;bottom:4px;height:10px;border-radius:5px;background:var(--green);font-size:5.5px;font-weight:700;line-height:10px}
.testimonials{position:absolute;left:378px;top:88px;width:279px}
.testimonial{display:flex;height:49px;margin-bottom:3px}
.testimonial .photo{position:relative;width:65px;height:100%}
.testimonial blockquote{flex:1;color:#fff;font-size:5.7px;line-height:8px;padding:11px 16px 0 20px;position:relative}
.testimonial blockquote::before{content:"\201C";position:absolute;left:6px;top:6px;font-size:14px;opacity:.5}
.testimonial blockquote::after{content:"\201D";position:absolute;right:6px;bottom:0;font-size:14px;opacity:.5}
.testimonial--green blockquote{background:var(--green)}
.testimonial--purple blockquote{background:var(--purple)}
.steps{position:absolute;left:370px;top:375px;width:300px;display:flex;justify-content:space-between}
.step{width:72px;text-align:center}
.step .icon{width:30px;height:30px;border-radius:50%;border:2px solid var(--green);margin:0 auto;display:flex;align-items:center;justify-content:center;background:#fff}
.step h6{font-size:6.8px;font-weight:600;color:var(--purple);line-height:8.5px;margin-top:8px;height:17px}
.step .rule{position:relative;display:block;margin:3px auto 4px;width:8px;height:2px}
.step p{font-size:4.2px;line-height:5.8px;color:#555}
.bottom-line{position:absolute;left:0;right:0;bottom:0;height:3px;background:var(--purple)}
.fold-line{position:absolute;left:347px;top:0;width:2px;height:100%;background:rgba(0,0,0,.05)}
</style>
</head>
<body>

<section class="spread spread--outer">
  <div class="photo" role="img" aria-label="Photo of a yellow labrador lying on a path with a couple sitting behind it" style="left:0;top:0;width:348px;height:331px;background:linear-gradient(160deg,#7c8a5a 0%,#a7a796 40%,#6d6b66 75%,#4f4e4b 100%)"></div>
  <div class="photo" role="img" aria-label="Photo of a smiling woman hugging a fluffy red merle puppy" style="left:348px;top:0;width:348px;height:331px;background:linear-gradient(150deg,#dcdcd6 0%,#b88a62 40%,#e8dfd6 70%,#c9b4a0 100%)"></div>

  <div class="band band--back">
    <h3>WE'D LOVE TO HELP YOU!</h3>
    <ul class="contact">
      <li><svg width="6" height="6" viewBox="0 0 10 10"><circle cx="5" cy="5" r="4" fill="none" stroke="#fff" stroke-width="1.2"/><path d="M5 2.5V5h2" fill="none" stroke="#fff" stroke-width="1.2"/></svg>Mon-Fri: 8 am - 6 pm</li>
      <li><svg width="6" height="6" viewBox="0 0 10 10"><path d="M2.5 1.5l1.5 2-1 1a5 5 0 0 0 2.5 2.5l1-1 2 1.5-1 1.5C5 9 1 5 1 2.5z" fill="#fff"/></svg>201-555-0142</li>
      <li><svg width="7" height="5" viewBox="0 0 12 8"><rect x=".5" y=".5" width="11" height="7" fill="none" stroke="#fff"/><path d="M.5.5l5.5 4 5.5-4" fill="none" stroke="#fff"/></svg>hello@hollowbrookpawcare.com</li>
    </ul>
    <p class="reviews">Check out our reviews on:</p>
    <div class="review-dots"><span></span><span></span><span></span></div>
    <p class="url">www.hollowbrookpawcare.com</p>
  </div>

  <div class="band band--front">
    <p class="tagline-small">Prioritize Your Family.</p>
    <p class="tagline-big">We'll Focus on Your Pets.</p>
    <p class="url">www.hollowbrookpawcare.com</p>
  </div>

  <div class="badge"><span>HOLLOWBROOK<br>PAW CARE</span></div>
  <div class="fold-corner"></div>
</section>

<section class="spread spread--inner">
  <div class="fold-line"></div>

  <h2 class="heading" style="left:30px;top:26px">LIFE IS A <em>BALANCING ACT.</em></h2>
  <span class="rule" style="left:30px;top:48px"></span>
  <p class="lead" style="left:30px;top:58px;width:276px">With Hollowbrook Paw Care, you will be able to focus on your life without sacrificing the needs of your pets. We offer a complimentary consultation and an online client portal/app to ensure that your pet's information is always up-to-date and scheduling is hassle-free. Let us afford you the luxury of time—life's greatest commodity—so you can effortlessly navigate life's to-do list.</p>

  <div class="mission">
    <h4>We're on a Mission</h4>
    <p>We promise to improve your pet's quality of life by consistently providing the highest level of pet care. We are dedicated to providing your pets a safe, comfortable and caring experience. We promise to keep your pet happy and healthy while providing you peace of mind.</p>
    <h4>Support Local</h4>
    <p>We are a small business that has served the Wrenfield community for close to 15 years! We give back to our community by helping local charitable organizations. We support the local economy by hiring employees and networking with other small businesses to build meaningful relationships.</p>
  </div>
  <div class="photo" role="img" aria-label="Photo of a tabby cat being petted and resting contentedly" style="left:190px;top:115px;width:158px;height:214px;background:linear-gradient(135deg,#e9e4e4 0%,#b9a596 35%,#8c7b6f 60%,#cfa58e 100%)"></div>

  <div class="services">
    <article class="service">
      <div class="photo" role="img" aria-label="Photo of a dog holding its leash in its mouth" style="background:linear-gradient(180deg,#d9cfc4,#8b6a4f)"></div>
      <h5>DOG WALKING</h5>
      <p>Mid-day dog walks keep your stay-at-home pup entertained while you attend to work or a day of play!</p>
      <span class="pill">I WORK!</span>
    </article>
    <article class="service">
      <div class="photo" role="img" aria-label="Photo of a small dog sitting in a packed suitcase" style="background:linear-gradient(180deg,#c9c2b8,#6f7a86)"></div>
      <h5>BOARDING</h5>
      <p>Leave your dogs with us and your guilt at the door. Devote your attention to your travels while we love on your pups!</p>
      <span class="pill">I TRAVEL!</span>
    </article>
    <article class="service">
      <div class="photo" role="img" aria-label="Photo of a pet sitter relaxing at home with a dog and cat" style="background:linear-gradient(180deg,#e7e2dc,#a38a74)"></div>
      <h5>PET SITTING</h5>
      <p>Pet care services in your home allow you to focus on fun knowing that your pets are being well-cared for.</p>
      <span class="pill">I'M ACTIVE!</span>
    </article>
  </div>

  <h2 class="heading" style="left:378px;top:26px">HERE'S WHAT OUR <em>CLIENTS SAY.</em></h2>
  <span class="rule" style="left:378px;top:48px"></span>
  <p class="lead" style="left:378px;top:58px;width:290px">We love our Clients! Our Clients love us back! We strive to maintain our impeccable reputation; check out our reviews on Searchly and Localist and feel the love!</p>

  <div class="testimonials">
    <div class="testimonial testimonial--green">
      <div class="photo" role="img" aria-label="Photo of a black and white collie mix" style="background:linear-gradient(160deg,#9aa3a6,#2c2c2c)"></div>
      <blockquote>You all not only take such great care of our most precious family member, you take such great care of us too by giving us such enjoyment and comfort from these daily reports and photos!</blockquote>
    </div>
    <div class="testimonial testimonial--purple">
      <div class="photo" role="img" aria-label="Photo of a black and white dog sitting outdoors" style="background:linear-gradient(160deg,#7d8a8f,#3a3a3a)"></div>
      <blockquote>I can't believe that I am lucky enough to have someone I trust on this level with my dog. There aren't enough words to recommend this business as much as I'd like to.</blockquote>
    </div>
    <div class="testimonial testimonial--green">
      <div class="photo" role="img" aria-label="Photo of a fluffy apricot poodle mix" style="background:linear-gradient(160deg,#b28a5e,#e2c39a)"></div>
      <blockquote>I schedule my travel and vacation around their availability. I will not let anyone else watch my crazy 4-legged baby!</blockquote>
    </div>
    <div class="testimonial testimonial--purple">
      <div class="photo" role="img" aria-label="Photo of a golden retriever in a garden" style="background:linear-gradient(160deg,#4f6b3a,#c98b3f)"></div>
      <blockquote>Hands down the best! Extremely friendly, reliable, and professional...flexible and easy to work with around crazy schedules.</blockquote>
    </div>
  </div>

  <h2 class="heading" style="left:378px;top:309px">READY TO FREE UP <em>YOUR TIME?</em></h2>
  <span class="rule" style="left:378px;top:331px"></span>
  <p class="lead" style="left:378px;top:341px;width:290px">We are here to uncomplicate your life! Our systems and processes allow for seamless scheduling, service and billing. Give us a few minutes of your time and we will deliver it back to you tenfold!</p>

  <div class="steps">
    <div class="step">
      <div class="icon"><svg width="16" height="14" viewBox="0 0 16 14"><rect x="1" y="1" width="14" height="9" fill="none" stroke="#5a4566" stroke-width="1.4"/><path d="M5 13h6M8 10v3" stroke="#5a4566" stroke-width="1.4"/></svg></div>
      <h6>Online<br>Registration</h6><span class="rule"></span>
      <p>Click the register link on our homepage to begin online registration or submit a request form if you would like more information first.</p>
    </div>
    <div class="step">
      <div class="icon"><svg width="16" height="14" viewBox="0 0 16 14"><path d="M2 2h12v8H7l-3 3v-3H2z" fill="#5a4566"/></svg></div>
      <h6>Complimentary<br>Consultation</h6><span class="rule"></span>
      <p>Request a consultation through our online portal. We'll reach out to you if you get stuck, then coordinate a meeting at your convenience.</p>
    </div>
    <div class="step">
      <div class="icon"><svg width="14" height="14" viewBox="0 0 14 14"><rect x="1" y="2" width="12" height="11" fill="none" stroke="#5a4566" stroke-width="1.4"/><path d="M1 5h12M4 1v3M10 1v3" stroke="#5a4566" stroke-width="1.4"/></svg></div>
      <h6>Flexible<br>Scheduling</h6><span class="rule"></span>
      <p>Once we've met, we will build a custom schedule for your visits. You can always adjust it through our portal app as your needs change.</p>
    </div>
    <div class="step">
      <div class="icon"><svg width="16" height="13" viewBox="0 0 16 13"><path d="M1 3h4l1.5-2h3L11 3h4v9H1z" fill="#5a4566"/><circle cx="8" cy="7.5" r="2.6" fill="#fff"/></svg></div>
      <h6>Visits with Reports<br>and Photos</h6><span class="rule"></span>
      <p>Your pets will be cared for by our team of pet care specialists. After each visit you will receive an emailed report with photos.</p>
    </div>
  </div>

  <div class="bottom-line"></div>
</section>

</body>
</html>
```